Business card design Needed for new logo / Construction business, home extensions and new builds

We need a business card design using our new logo files which i will attach to this project :)

We are a small construction business specialising in home extensions, new builds and property development. We are very ambitious and would appreciate professional and elegant designs for our new business card.

Very serious about using the services on MakerQuarry and recently acquired our new logo from here :)

Please get involved, i will feedback when i can as i am very busy but can respond daily, thanks

Target Market(s)

People that want to build onto their houses, new building developments or adding too their existing property

Industry/Entity Type

Construction

Contact Information for Business Card

Renwick Tolliver Construction, Lionel Ashby (Managing Director), Tel 07822254961, email - info@renwick-tolliver, www.renwick-tolliver.co.uk

Colors

Designer to choose colors to be used in the design.

Requirements
Must have
• I like a deep grey on the back please. A lot of you have provided black from and back, try mixing things up a little. The black looks cool 😎 Thanks

```html
<!DOCTYPE html>
<html lang="en">
<head>
<meta charset="utf-8">
<title>Renwick Tolliver Construction – Business Card</title>
<link rel="stylesheet" href="https://fonts.googleapis.com/css2?family=Montserrat:wght@400;600&display=swap">
<style>
  :root {
    --canvas: #6e6e6e;
    --card-black: #0b0b0b;
    --card-deep-grey: #262626;
    --card-white: #ffffff;
    --gold: #d4a232;
    --text-light: #f2f2f2;
  }
  * { box-sizing: border-box; margin: 0; padding: 0; }
  html, body {
    width: 1200px; height: 1200px; overflow: hidden;
    background: var(--canvas);
    font-family: "Montserrat", Arial, sans-serif;
  }
  .stage {
    width: 1200px; height: 1200px;
    display: flex; flex-direction: column; align-items: center; justify-content: center;
    gap: 70px;
  }
  .card {
    width: 770px; height: 440px;
    border-radius: 34px;
    overflow: hidden;
    position: relative;
    box-shadow: 0 18px 40px rgba(0,0,0,.4);
  }
  /* Front */
  .card-front { display: flex; background: var(--card-white); }
  .front-info {
    width: 50%; height: 100%;
    background: var(--card-black);
    border-right: 7px solid var(--gold);
    display: flex; flex-direction: column; justify-content: center;
    padding-left: 66px;
  }
  .identity {
    border-left: 6px solid var(--gold);
    padding-left: 14px;
    margin-bottom: 26px;
  }
  .person-name {
    color: var(--gold); font-weight: 600; font-size: 25px; letter-spacing: .5px;
    text-transform: uppercase; line-height: 1.15;
  }
  .person-title {
    color: var(--text-light); font-size: 14px; letter-spacing: 1px;
    text-transform: uppercase;
  }
  .contact-list { list-style: none; display: flex; flex-direction: column; gap: 12px; }
  .contact-item {
    display: flex; align-items: center; gap: 14px;
    color: var(--text-light); font-size: 17px; white-space: nowrap;
  }
  .contact-icon { width: 22px; height: 22px; flex: none; }
  .front-brand {
    flex: 1; display: flex; align-items: center; justify-content: center;
    padding-bottom: 30px;
  }
  /* Brand lockup */
  .brand {
    display: flex; flex-direction: column; align-items: center; gap: 14px;
    color: var(--gold); font-weight: 600; text-align: center;
    text-transform: uppercase;
  }
  .brand-mark { width: 22px; height: 22px; background: var(--gold); }
  .brand-name { letter-spacing: 2px; line-height: 1.25; }
  .front-brand .brand-name { font-size: 22px; }
  /* Back */
  .card-back {
    background: var(--card-deep-grey);
    display: flex; align-items: center; justify-content: center;
  }
  .card-back .brand-mark { width: 34px; height: 34px; }
  .card-back .brand-name { font-size: 36px; letter-spacing: 3px; }
</style>
</head>
<body>
<main class="stage">
  <section class="card card-front">
    <div class="front-info">
      <div class="identity">
        <p class="person-name">Lionel Ashby</p>
        <p class="person-title">Managing Director</p>
      </div>
      <ul class="contact-list">
        <li class="contact-item">
          <svg class="contact-icon" viewBox="0 0 24 24"><path fill="var(--gold)" d="M6.6 10.8a15.1 15.1 0 0 0 6.6 6.6l2.2-2.2c.3-.3.7-.4 1-.2 1.1.4 2.3.6 3.6.6.6 0 1 .4 1 1V20c0 .6-.4 1-1 1C10.6 21 3 13.4 3 4c0-.6.4-1 1-1h3.5c.6 0 1 .4 1 1 0 1.3.2 2.5.6 3.6.1.3 0 .7-.2 1z"/></svg>
          <span>+44 7822 254 961</span>
        </li>
        <li class="contact-item">
          <svg class="contact-icon" viewBox="0 0 24 24"><rect x="2" y="5" width="20" height="14" fill="var(--gold)"/><path d="M2 5l10 8 10-8" fill="none" stroke="var(--card-black)" stroke-width="1.6"/></svg>
          <span>info@renwick-tolliver.co.uk</span>
        </li>
        <li class="contact-item">
          <svg class="contact-icon" viewBox="0 0 24 24" fill="none" stroke="var(--gold)" stroke-width="1.8"><circle cx="12" cy="12" r="9.5"/><ellipse cx="12" cy="12" rx="4" ry="9.5"/><path d="M2.5 12h19M4 7h16M4 17h16"/></svg>
          <span>www.renwick-tolliver.co.uk</span>
        </li>
      </ul>
    </div>
    <div class="front-brand">
      <div class="brand">
        <span class="brand-mark"></span>
        <p class="brand-name">Renwick Tolliver<br>Construction</p>
      </div>
    </div>
  </section>

  <section class="card card-back">
    <div class="brand">
      <span class="brand-mark"></span>
      <p class="brand-name">Renwick Tolliver<br>Construction</p>
    </div>
  </section>
</main>
</body>
</html>
```